Website for steady harbor detailing.

Need a homepage, pages for: car and truck detailing, boat detailing, airplane detailing, about us, contact us. I have the domain name through nimbushelm so I will need the design uploaded on my domain. Also hoping to link other domains to this page.I would like to see the logo more pronounced. I would like to see a large phone number link to call my business. The layout looks nice but the pics need to depict car washing and waxing not car mechanics. i would like the colors of the webpage to incorporate the colors found in the logo in some way. I would like links to social media pages
Updates

Target Market(s)

Local customers in Vero Beach, Florida.

Number of Pages Required

5+ page

Colors

Requirements
Must have
• Easy to navigate, attractive pages with pictures and logo, professional looking. must have my phone number and logo very prevalent and links to call or go to home page. I would like links to my social media accounts on the home page.
Nice to have
• Easy to navigate, attractive pages with pictures and logo, professional looking.

```html
<!DOCTYPE html>
<html lang="en">
<head>
<meta charset="utf-8">
<title>Steady Harbor Detailing</title>
<link href="https://fonts.googleapis.com/css2?family=PT+Sans:ital,wght@0,400;0,700;1,400&family=Roboto+Slab:wght@400;700&display=swap" rel="stylesheet">
<style>
:root{
  --red:#e8131f;
  --navy:#232a7e;
  --ink:#1d1d1d;
  --text:#555;
  --band:#ebecef;
  --footer:#2e2e2e;
  --footer-base:#232323;
  --white:#fff;
}
*{margin:0;padding:0;box-sizing:border-box}
html,body{width:1200px;height:3015px;overflow:hidden}
body{position:relative;background:var(--white);font-family:"PT Sans",Arial,sans-serif;color:var(--ink)}
.slab{font-family:"Roboto Slab",Georgia,serif}

/* header */
.site-header{position:absolute;left:0;top:0;width:1200px;height:78px;background:var(--white);border-bottom:3px solid var(--red)}
.brand{position:absolute;left:202px;top:8px;display:flex;align-items:center;gap:10px}
.brand-mark{width:38px;height:38px;border-radius:50%;background:var(--red);flex:none}
.brand-name{font-weight:700;font-size:21px;color:var(--navy);line-height:1.02;width:170px}
.brand-phone{position:absolute;left:250px;top:56px;font-size:11px;color:var(--red);letter-spacing:2px;font-weight:700}
.brand-divider{position:absolute;left:424px;top:0;width:1px;height:76px;background:#ddd}
.main-nav{position:absolute;left:456px;top:30px;display:flex;gap:26px;font-size:12px;text-transform:uppercase;color:#333}
.main-nav .active{color:var(--red)}
.call-btn{position:absolute;left:834px;top:12px;width:170px;height:50px;background:var(--red);color:var(--white);font-size:13px;font-weight:700;display:flex;align-items:center;justify-content:center;gap:10px}

/* hero */
.hero-photo{position:absolute;left:0;top:78px;width:1200px;height:588px;
  background:
    linear-gradient(200deg,rgba(120,160,205,.85) 0%,rgba(170,195,220,.4) 22%,rgba(255,255,255,0) 40%),
    linear-gradient(180deg,#e9ecef 0%,#f7f8f8 30%,#dfe3e6 48%,#5d6670 56%,#eef0f1 62%,#d3d8dc 80%,#8b939b 100%)}
.hero-card{position:absolute;left:200px;top:262px;width:410px;height:248px;background:rgba(255,255,255,.6);border-left:5px solid var(--navy);padding:24px 0 0 30px}
.hero-card h1{font-family:"Roboto Slab",Georgia,serif;color:var(--navy);font-size:32px;line-height:1.2;font-weight:700}
.hero-card p{font-size:13px;line-height:1.45;margin-top:10px;width:340px;color:#222}
.btn{display:inline-flex;align-items:center;justify-content:center;color:var(--white);font-size:12px;font-weight:700;height:38px}
.btn-red{background:var(--red)}
.btn-navy{background:var(--navy)}
.hero-actions{position:absolute;left:30px;top:166px;display:flex;gap:8px}
.hero-actions .btn{width:94px}
.slide-arrow{position:absolute;top:352px;width:42px;height:44px;background:#111;display:flex;align-items:center;justify-content:center}

/* welcome */
.welcome{position:absolute;left:0;top:666px;width:1200px;height:164px;background:var(--band)}
.welcome h2{position:absolute;right:706px;top:48px;text-align:right;font-family:"Roboto Slab",Georgia,serif;font-size:23px;line-height:1.35;font-weight:400;letter-spacing:.5px;white-space:nowrap}
.welcome .rule{position:absolute;left:526px;top:48px;width:2px;height:60px;background:#333}
.welcome p{position:absolute;left:548px;top:46px;width:452px;font-size:11px;font-style:italic;line-height:1.8;color:#333}

/* services */
.section-title{position:absolute;font-family:"Roboto Slab",Georgia,serif;font-size:24px;font-weight:400;letter-spacing:.5px;padding-right:10px;border-right:2px solid #333;line-height:1}
.service{position:absolute;left:0;width:1200px;height:306px}
.service-photo{position:absolute;top:0;width:600px;height:306px}
.service-body{position:absolute;top:38px;width:370px}
.service-body h3{font-family:"Roboto Slab",Georgia,serif;font-size:20px;font-weight:400;margin-bottom:16px}
.service-body p{font-size:11px;line-height:1.65;color:var(--text)}
.service-links{display:flex;gap:18px;margin:14px 0 16px;font-size:13px}
.service-links span{display:flex;align-items:center;gap:6px}
.service-links .hot{color:var(--red)}
.service-body .btn{width:94px;margin-top:16px}
.right .service-body{text-align:right}
.right .service-links{justify-content:flex-end}

/* testimonial */
.testimonials{position:absolute;left:0;top:1936px;width:1200px;height:408px;background:var(--band)}
.avatar{position:absolute;left:552px;top:130px;width:96px;height:96px;background:radial-gradient(circle at 50% 40%,#e8cdb9 0 28%,#7a5a45 29% 36%,#bfe0e4 37%);border:3px solid var(--white)}
.quote{position:absolute;left:200px;top:258px;width:800px;text-align:center;font-size:14px;font-weight:700;line-height:1.6;color:#222}
.rating{position:absolute;left:514px;top:316px;font-size:13px;display:flex;gap:14px;align-items:center}
.stars{letter-spacing:2px;font-size:15px}
.dots{position:absolute;left:558px;top:360px;display:flex;gap:6px}
.dots i{width:16px;height:3px;background:#999}
.dots i:first-child{background:var(--red)}

/* partners */
.partners{position:absolute;left:0;top:2344px;width:1200px;height:160px;background:var(--band);border-top:1px solid #c7c7c7}
.partner-row{position:absolute;left:200px;top:56px;width:800px;display:flex;justify-content:space-between;align-items:center}
.partner{display:flex;align-items:center;gap:8px;font-size:22px;font-weight:700;color:#222}
.partner i{width:16px;height:16px;background:#222;border-radius:50%}

/* newsletter */
.newsletter-copy{position:absolute;left:200px;top:2616px;width:360px;font-size:11px;line-height:1.7;color:#333}
.subscribe{position:absolute;left:568px;top:2606px;width:432px;height:54px;display:flex;border:1px solid #ddd}
.subscribe .field{flex:1;display:flex;align-items:center;gap:10px;padding-left:16px;font-size:11px;color:#555}
.subscribe .send{width:116px;background:var(--red);color:var(--white);font-size:13px;font-weight:700;display:flex;align-items:center;justify-content:center}

/* footer */
.site-footer{position:absolute;left:0;top:2726px;width:1200px;height:242px;background:var(--footer);color:var(--white)}
.foot-col{position:absolute;top:58px;text-align:center;font-size:11px;line-height:2.2}
.foot-col h4{font-size:13px;font-weight:700;text-transform:uppercase;margin-bottom:10px;line-height:1}
.foot-col .mail{color:var(--red)}
.socials{display:flex;gap:6px;justify-content:center;margin-top:6px}
.social{width:24px;height:24px;border-radius:50%;background:var(--white);display:flex;align-items:center;justify-content:center}
.footer-base{position:absolute;left:0;top:2968px;width:1200px;height:47px;background:var(--footer-base);color:#ddd;font-size:11px}
.footer-base span{position:absolute;top:16px}
</style>
</head>
<body>

<header class="site-header">
  <div class="brand"><span class="brand-mark"></span><span class="brand-name">Steady Harbor Detailing</span></div>
  <div class="brand-phone">555 · 218 · 4630</div>
  <div class="brand-divider"></div>
  <nav class="main-nav"><span class="active">Home</span><span>About Us</span><span>Services</span><span>Clients</span><span>Contact Us</span></nav>
  <a class="call-btn">
    <svg width="18" height="18" viewBox="0 0 24 24"><path fill="#fff" d="M6.6 10.8a15 15 0 0 0 6.6 6.6l2.2-2.2c.3-.3.7-.4 1-.2 1.1.4 2.3.6 3.6.6.6 0 1 .4 1 1V20c0 .6-.4 1-1 1C10.6 21 3 13.4 3 4c0-.6.4-1 1-1h3.5c.6 0 1 .4 1 1 0 1.3.2 2.5.6 3.6.1.3 0 .7-.2 1z"/></svg>
    CALL : 555-218-4630
  </a>
</header>

<section class="hero">
  <div class="hero-photo" role="img" aria-label="Detailers washing the deck and hull of a large white yacht"></div>
  <div class="hero-card">
    <h1>we provide this service from 30 years</h1>
    <p>Lorem Ipsum is simply dummy text of the printing and typesetting industry. Lorem Ipsum is text...</p>
    <div class="hero-actions"><a class="btn btn-red">Read More</a><a class="btn btn-navy">Contact Us</a></div>
  </div>
  <div class="slide-arrow" style="left:0"><svg width="12" height="14"><path d="M10 1 2 7l8 6" fill="#fff"/></svg></div>
  <div class="slide-arrow" style="left:1158px"><svg width="12" height="14"><path d="M2 1l8 6-8 6" fill="#fff"/></svg></div>
</section>

<section class="welcome">
  <h2>WELCOME TO STEADY<br>HARBOR DETAILING</h2>
  <div class="rule"></div>
  <p>Lorem Ipsum is simply dummy text of the printing and typesetting industry. Lorem Ipsum has been the industry's standard dummy text ever since the 1500s, when an unknown printer took a galley of type and scrambled it</p>
</section>

<h2 class="section-title" style="left:200px;top:890px">OUR SERVICES</h2>

<article class="service" style="top:954px">
  <div class="service-photo" style="left:0;background:linear-gradient(180deg,#4a4037 0%,#8a7d6c 22%,#c9c3b6 40%,#5b5552 60%,#1e1d20 80%,#6d6862 100%)" role="img" aria-label="Man pressure washing a black sedan in a garage bay"></div>
  <div class="service-body" style="left:628px">
    <h3>Car Washing</h3>
    <p>Lorem Ipsum is simply dummy text of the printing and typesetting industry. Lorem Ipsum has been the industry's standard dummy text ever since the 1500s, when an unknown printer</p>
    <div class="service-links">
      <span class="hot"><svg width="24" height="14"><rect x="1" y="5" width="22" height="6" rx="2" fill="#e8131f"/><rect x="5" y="1" width="13" height="6" rx="2" fill="#e8131f"/><circle cx="6" cy="12" r="2" fill="#e8131f"/><circle cx="18" cy="12" r="2" fill="#e8131f"/></svg>Car Waxing</span>
      <span><svg width="24" height="14"><rect x="1" y="5" width="22" height="6" rx="2" fill="#111"/><rect x="5" y="1" width="13" height="6" rx="2" fill="#111"/><circle cx="6" cy="12" r="2" fill="#111"/><circle cx="18" cy="12" r="2" fill="#111"/></svg>Car Degrease</span>
    </div>
    <p>Lorem Ipsum is simply dummy text of the printing and typesetting industry. Lorem Ipsum has been the industry's</p>
    <a class="btn btn-navy">Read More</a>
  </div>
</article>

<article class="service right" style="top:1260px">
  <div class="service-photo" style="left:600px;background:linear-gradient(180deg,#9ab8d2 0%,#c9d6df 12%,#f4f5f3 30%,#e7ebe8 52%,#1f7a66 64%,#16564a 78%,#3b3a3a 100%)" role="img" aria-label="Worker pressure washing the hull of a boat"></div>
  <div class="service-body" style="left:206px">
    <h3>Boats</h3>
    <p>Lorem Ipsum is simply dummy text of the printing and typesetting industry. Lorem Ipsum has been the industry's standard dummy text ever since the 1500s, when an unknown printer</p>
    <div class="service-links">
      <span class="hot"><svg width="26" height="14"><path d="M1 8h24l-4 5H4z" fill="#e8131f"/><rect x="8" y="3" width="10" height="4" fill="#e8131f"/></svg>Boat Waxing</span>
      <span><svg width="26" height="14"><path d="M1 8h24l-4 5H4z" fill="#111"/><rect x="8" y="3" width="10" height="4" fill="#111"/></svg>Boat Degrease</span>
    </div>
    <p>Lorem Ipsum is simply dummy text of the printing and typesetting industry. Lorem Ipsum has been the industry's</p>
    <a class="btn btn-navy">Read More</a>
  </div>
</article>

<article class="service" style="top:1566px">
  <div class="service-photo" style="left:0;background:linear-gradient(180deg,#7f8fa3 0%,#aab3bd 30%,#d5d8da 50%,#9a9ea3 62%,#5e6166 80%,#44464a 100%)" role="img" aria-label="Passenger airliner parked at an airport jet bridge"></div>
  <div class="service-body" style="left:628px">
    <h3>Airplane</h3>
    <p>Lorem Ipsum is simply dummy text of the printing and typesetting industry. Lorem Ipsum has been the industry's standard dummy text ever since the 1500s, when an unknown printer</p>
    <div class="service-links">
      <span class="hot"><svg width="26" height="14"><path d="M1 7h24M10 7 6 1M10 7 6 13M22 7l2-4" stroke="#e8131f" stroke-width="3" fill="none"/></svg>Airplane Waxing</span>
      <span><svg width="26" height="14"><path d="M1 7h24M10 7 6 1M10 7 6 13M22 7l2-4" stroke="#111" stroke-width="3" fill="none"/></svg>Airplane Degrease</span>
    </div>
    <p>Lorem Ipsum is simply dummy text of the printing and typesetting industry. Lorem Ipsum has been the industry's</p>
    <a class="btn btn-navy">Read More</a>
  </div>
</article>

<section class="testimonials">
  <h2 class="slab" style="position:absolute;left:0;width:1200px;top:68px;text-align:center;font-size:22px;font-weight:400">WHAT OUR CLIENT SAY</h2>
  <div class="avatar" role="img" aria-label="Portrait photo of the client"></div>
  <p class="quote">Lorem Ipsum is simply dummy text of the printing and typesetting industry. Lorem Ipsum has been the industry's standard dummy text ever since the 1500s, when an unknown printer took a galley of type</p>
  <div class="rating"><span class="stars">★★★★★</span><span>- Marla Quinn</span></div>
  <div class="dots"><i></i><i></i><i></i><i></i></div>
</section>

<section class="partners">
  <div class="partner-row">
    <span class="partner">Ridgeform</span>
    <span class="partner"><i></i>Oakframe</span>
    <span class="partner">Placeholdr</span>
    <span class="partner"><i></i>Brightvale</span>
    <span class="partner">Millworks</span>
  </div>
</section>

<section class="newsletter">
  <h2 class="section-title" style="left:200px;top:2574px">OUR NEWSLETTER</h2>
  <p class="newsletter-copy">Lorem Ipsum is simply dummy text of the printing and typesetting industry. Lorem Ipsum standard dummy text</p>
  <div class="subscribe">
    <div class="field"><svg width="22" height="18"><rect x="1" y="3" width="20" height="14" fill="#f0b429"/><path d="M1 3l10 8 10-8" stroke="#fff" fill="none"/></svg>Enter Your E-mail</div>
    <div class="send">SEND</div>
  </div>
</section>

<footer class="site-footer">
  <div class="foot-col" style="left:196px;width:70px"><h4>Company</h4>About Us<br>Services<br>Clients<br>Contact Us</div>
  <div class="foot-col" style="left:350px;width:100px"><h4>Quick Links</h4>Site Map<br>Help<br>Privacy Policy<br>Contact</div>
  <div class="foot-col" style="left:510px;width:234px"><h4>Contact</h4><span class="mail">info@steadyharbordetailing.com</span><br>Call : 555-218-4630
    <div class="socials">
      <a class="social" aria-label="Social page"><svg width="12" height="12" viewBox="0 0 12 12"><circle cx="3" cy="6" r="2" fill="#2e2e2e"/><circle cx="9.5" cy="2.5" r="2" fill="#2e2e2e"/><circle cx="9.5" cy="9.5" r="2" fill="#2e2e2e"/><path d="M3 6l6.5-3.5M3 6l6.5 3.5" stroke="#2e2e2e" stroke-width="1.2"/></svg></a>
      <a class="social" aria-label="Social page"><svg width="12" height="12" viewBox="0 0 12 12"><path d="M6 11S1.5 7.6 1.5 4.5a2.3 2.3 0 0 1 4.5-.9 2.3 2.3 0 0 1 4.5.9C10.5 7.6 6 11 6 11z" fill="#2e2e2e"/></svg></a>
      <a class="social" aria-label="Social page"><svg width="12" height="12" viewBox="0 0 12 12"><rect x="1" y="2" width="10" height="7" rx="1.5" fill="#2e2e2e"/><path d="M3 9v2.5L5.5 9" fill="#2e2e2e"/></svg></a>
      <a class="social" aria-label="Social page"><svg width="12" height="12" viewBox="0 0 12 12"><circle cx="6" cy="6" r="4.5" fill="none" stroke="#2e2e2e" stroke-width="1.4"/><path d="M1.5 6h9M6 1.5c2 2.5 2 6.5 0 9M6 1.5c-2 2.5-2 6.5 0 9" stroke="#2e2e2e" fill="none"/></svg></a>
    </div></div>
  <div class="foot-col" style="left:826px;width:170px;line-height:1.8"><h4 style="margin-bottom:16px">Location</h4>Lorem Ipsum is simply dummy text of the printing and typesetting industry. text here..</div>
</footer>
<div class="footer-base"><span style="left:200px">© Copyright 2018 steady harbor detailing. All Rights Reserved.</span><span style="right:200px">Terms and Condition</span></div>

</body>
</html>
```